Beacon Advisory Website

I currently have a website www.beaconadvisoryinc.com. We are a IT Consulting Company. Our website will pretty much tell out our services. I am looking to enhance my website and make it look more professional. Looking for very classy and Contemporary look and design for my website.

It Company

```html
<!DOCTYPE html>
<html lang="en">
<head>
<meta charset="utf-8">
<title>Beacon Advisory</title>
<link href="https://fonts.googleapis.com/css2?family=Arimo:wght@400;700&family=Open+Sans:ital,wght@0,400;0,600;0,700;1,400&display=swap" rel="stylesheet">
<style>
:root{
  --blue:#1a9ad6;
  --blue-dark:#145a9e;
  --navy:#1f2a3a;
  --ink:#222;
  --muted:#666;
  --line:#e4e4e4;
  --pale:#eef2f5;
  --white:#fff;
}
*{margin:0;padding:0;box-sizing:border-box}
html,body{width:800px;height:1200px;overflow:hidden}
body{position:relative;background:var(--white);font-family:"Open Sans",Arial,sans-serif;color:var(--ink)}
.abs{position:absolute}

/* header */
.site-header{position:absolute;left:0;top:0;width:800px;height:70px;border-top:3px solid var(--blue);background:var(--white)}
.brand{position:absolute;display:flex;align-items:center;gap:7px;font-family:"Arimo",Arial,sans-serif;font-weight:700;color:var(--blue-dark);font-size:15px;letter-spacing:.5px;white-space:nowrap}
.brand-dot{width:22px;height:22px;border-radius:50%;background:var(--blue-dark);flex:none}
.header-brand{left:62px;top:22px}
.header-phone{position:absolute;left:616px;top:9px;display:flex;align-items:center;gap:6px;color:var(--blue);font-family:"Arimo",Arial,sans-serif;font-size:12px;white-space:nowrap}
.phone-ring{width:24px;height:24px;border:1px solid #bbb;border-radius:50%;display:flex;align-items:center;justify-content:center}
.main-nav{position:absolute;top:0;left:0;width:800px;height:70px;font-family:"Arimo",Arial,sans-serif;font-weight:700;font-size:8.8px}
.main-nav a{position:absolute;top:44px;color:var(--ink);text-decoration:none;white-space:nowrap}
.main-nav a.active{color:var(--blue)}
.search-icon{position:absolute;left:726px;top:45px}

/* hero */
.hero{position:absolute;left:0;top:70px;width:800px;height:286px;background:linear-gradient(90deg,#24384f 0%,#3a6b94 28%,#5aa6d8 52%,#7cc2ec 100%)}
.hero-title{position:absolute;left:460px;top:70px;font-family:"Arimo",Arial,sans-serif;font-weight:700;font-size:26.5px;color:var(--white);letter-spacing:.3px;white-space:nowrap}
.hero-text{position:absolute;left:460px;top:108px;width:280px;font-style:italic;font-size:10px;line-height:19px;color:var(--white)}
.btn-outline{position:absolute;left:461px;top:179px;width:124px;height:30px;border:2px solid var(--white);background:var(--blue);color:var(--white);font-family:"Arimo",Arial,sans-serif;font-weight:700;font-size:10.5px;display:flex;align-items:center;justify-content:center}
.dots{position:absolute;left:377px;top:248px;display:flex;gap:2px}
.dots span{width:10px;height:10px;border-radius:50%;border:1.5px solid var(--white)}
.dots span.on{background:var(--blue)}

/* section headings */
.section-title{position:absolute;left:0;width:800px;display:flex;justify-content:center;align-items:center;gap:8px;font-family:"Arimo",Arial,sans-serif;font-weight:700;font-size:13px;color:var(--ink)}
.section-title em{font-style:normal;color:var(--blue-dark)}
.title-dot{width:16px;height:16px;border-radius:50%;background:var(--blue-dark)}

/* welcome */
.intro{position:absolute;left:122px;top:418px;width:556px;text-align:center;font-size:7.9px;line-height:16px;color:var(--muted)}
.feature{position:absolute;top:500px;width:186px;height:92px;border:3px solid #eee;background:var(--white);padding:10px 10px 0 41px}
.feature h3{font-family:"Arimo",Arial,sans-serif;font-size:10.5px;font-weight:700;color:var(--ink);margin-bottom:6px}
.feature p{font-size:8px;line-height:13.5px;color:var(--muted)}
.feature .more{display:block;margin-top:6px;font-size:7.5px;font-weight:700;color:var(--blue)}
.feature-icon{position:absolute;top:517px;width:58px;height:58px;border-radius:50%;background:var(--blue);display:flex;align-items:center;justify-content:center}

/* services */
.services{position:absolute;left:0;top:620px;width:800px;height:242px;background:var(--pale)}
.service-card{position:absolute;top:690px;width:160px;height:139px;background:var(--white);border:1px solid #e2e2e2;padding:3px}
.service-card .pic{width:152px;height:104px}
.service-card h4{font-family:"Arimo",Arial,sans-serif;font-weight:700;font-size:10.5px;color:#333;text-align:center;margin-top:11px;white-space:nowrap}

/* testimonial */
.quote-bg{position:absolute;left:92px;top:892px;width:72px;height:72px;border-radius:50%;background:#e8e8e8;display:flex;align-items:center;padding-left:10px;font-family:Georgia,serif;font-size:44px;font-weight:700;color:#cfcfcf}
.avatar{position:absolute;left:138px;top:892px;width:74px;height:74px;border-radius:50%;background:radial-gradient(circle at 50% 40%,#d7dde3,#7c8896)}
.quote-text{position:absolute;left:234px;top:892px;width:470px;font-style:italic;font-size:8.4px;line-height:18.5px;color:#777}
.quote-name{position:absolute;left:234px;top:956px;font-weight:600;font-size:10px;color:var(--blue)}

/* footer */
.site-footer{position:absolute;left:0;top:998px;width:800px;height:202px;background:var(--navy);color:#dfe5ec}
.footer-brand{left:84px;top:56px;color:var(--white);font-size:12.5px;gap:6px}
.footer-brand .brand-dot{background:var(--white);width:18px;height:18px}
.col-title{position:absolute;top:22px;font-family:"Arimo",Arial,sans-serif;font-weight:700;font-size:10.5px;color:var(--white)}
.col-rule{position:absolute;top:24px;width:1px;height:120px;background:#2e3a4b}
.info-links{position:absolute;left:268px;top:49px;list-style:none;font-size:8px;line-height:13.1px}
.news-text{position:absolute;left:387px;top:51px;font-size:8px;line-height:12.5px;width:140px}
.news-input{position:absolute;left:387px;top:81px;width:175px;height:22px;background:var(--white);color:#777;font-size:8px;padding:6px 8px}
.btn-subscribe{position:absolute;left:387px;top:111px;width:67px;height:24px;border:1.5px solid var(--white);background:var(--blue);color:var(--white);font-weight:700;font-size:8.5px;display:flex;align-items:center;justify-content:center}
.contact-row{position:absolute;left:607px;display:flex;gap:9px;font-size:8px;line-height:13px;white-space:nowrap}
.contact-row svg{flex:none;margin-top:2px}
.footer-rule{position:absolute;left:66px;top:153px;width:668px;height:1px;background:#2e3a4b}
.copyright{position:absolute;left:66px;top:172px;font-size:8px}
.socials{position:absolute;left:624px;top:166px;display:flex;gap:5px}
.socials span{width:24px;height:24px;border-radius:50%;border:1.5px solid var(--white)}
</style>
</head>
<body>

<header class="site-header">
  <div class="brand header-brand"><span class="brand-dot"></span>BEACON ADVISORY</div>
  <div class="header-phone">
    <span class="phone-ring">
      <svg width="12" height="12" viewBox="0 0 24 24"><path fill="#999" d="M6.6 10.8a15.1 15.1 0 0 0 6.6 6.6l2.2-2.2c.3-.3.7-.4 1-.2 1.1.4 2.3.6 3.6.6.6 0 1 .4 1 1V20c0 .6-.4 1-1 1A17 17 0 0 1 3 4c0-.6.4-1 1-1h3.5c.6 0 1 .4 1 1 0 1.3.2 2.5.6 3.6.1.3 0 .7-.2 1z"/></svg>
    </span>
    +1 (555) 014 2290
  </div>
  <nav class="main-nav">
    <a class="active" style="left:299px">HOME</a>
    <a style="left:342px">COMPANY</a>
    <a style="left:404px">SERVICES</a>
    <a style="left:463px">SOLUTIONS</a>
    <a style="left:530px">RESOURCES</a>
    <a style="left:600px">CAREER</a>
    <a style="left:653px">CONTACT US</a>
  </nav>
  <svg class="search-icon" width="9" height="9" viewBox="0 0 10 10"><circle cx="4" cy="4" r="3" fill="none" stroke="#222" stroke-width="1.5"/><line x1="6.2" y1="6.2" x2="9.2" y2="9.2" stroke="#222" stroke-width="1.6"/></svg>
</header>

<section class="hero" role="img" aria-label="Photo of a hand holding a magnifying glass over a network of people icons on a blue background">
  <h1 class="hero-title">BEACON ADVISORY</h1>
  <p class="hero-text">Beacon Advisory maintains a global presence, aggressively recruiting expertly qualified IT and Management Professionals from around the world</p>
  <div class="btn-outline">GET A FREE QUOTE</div>
  <div class="dots"><span class="on"></span><span></span><span></span><span></span></div>
</section>

<h2 class="section-title" style="top:385px"><span class="title-dot"></span>WELCOME TO <em>BEACON ADVISORY</em></h2>
<p class="intro">Today's IT market is a dynamic, fast-paced industry, with ever-increasing demands. Meeting these demands for over 25 years, Beacon Advisory maintains a global presence, aggressively recruiting expertly qualified IT and Management Professionals from around the world and cultivating key partnerships with corporations to understand their business models end-to-end, with a goal of delivering exceptional client service and ensuring a consistent delivery of the talent needed to drive results.</p>

<div class="feature" style="left:92px"><h3>Consulting</h3><p>Beacon Advisory has certified professional consultants to work..</p><span class="more">READ MORE &gt;&gt;</span></div>
<div class="feature" style="left:320px"><h3>Staff Augmentation</h3><p>For years Beacon Advisory as been offering our customers..</p><span class="more">READ MORE &gt;&gt;</span></div>
<div class="feature" style="left:548px"><h3>Offshore</h3><p>Our Offshore development model has a unique distinction ..</p><span class="more">READ MORE &gt;&gt;</span></div>

<div class="feature-icon" style="left:66px">
  <svg width="32" height="28" viewBox="0 0 32 28"><ellipse cx="14" cy="11" rx="12" ry="9" fill="none" stroke="#fff" stroke-width="2.5"/><path d="M6 18l-3 6 8-4" fill="#fff"/><path d="M26 10c4 2 5 7 1 10l2 5-6-3" fill="none" stroke="#fff" stroke-width="2.5"/></svg>
</div>
<div class="feature-icon" style="left:295px">
  <svg width="32" height="26" viewBox="0 0 32 26"><circle cx="16" cy="7" r="5" fill="#fff"/><circle cx="6" cy="9" r="3.5" fill="#fff"/><circle cx="26" cy="9" r="3.5" fill="#fff"/><path d="M8 25c0-7 3.5-11 8-11s8 4 8 11z" fill="#fff"/><path d="M0 22c0-5 2.5-8 6-8 1 0 2 .3 2.8 1C7.6 17 7 19.5 7 22z" fill="#fff"/><path d="M32 22c0-5-2.5-8-6-8-1 0-2 .3-2.8 1 1.2 2 1.8 4.5 1.8 7z" fill="#fff"/></svg>
</div>
<div class="feature-icon" style="left:523px">
  <svg width="30" height="30" viewBox="0 0 30 30"><circle cx="15" cy="15" r="14" fill="#fff"/><path d="M8 8c3-1 5 1 6 3s-1 4-3 5-1 4-3 4-3-3-3-6 1-5 3-6zm11 3c2 0 4 2 4 4s-2 3-3 5-3 2-3 0 0-3-1-5 1-4 3-4z" fill="#1a9ad6"/></svg>
</div>

<section class="services" aria-label="Our services"></section>
<h2 class="section-title" style="top:647px"><span class="title-dot"></span>OUR <em>SERVICES</em></h2>

<div class="service-card" style="left:66px"><div class="pic" role="img" aria-label="Businessman touching a glowing digital interface" style="background:linear-gradient(135deg,#1d2430,#4a5566 60%,#2a3240)"></div><h4>Technology &amp; Application</h4></div>
<div class="service-card" style="left:235px"><div class="pic" role="img" aria-label="Team meeting in front of a chart on a screen" style="background:linear-gradient(180deg,#d9dde2,#9aa5b0 60%,#6a5a50)"></div><h4>Business &amp; Consulting</h4></div>
<div class="service-card" style="left:404px"><div class="pic" role="img" aria-label="Hands holding a tablet with charts over printed reports" style="background:linear-gradient(135deg,#e7edf3,#8fb4d6 55%,#3d6f9e)"></div><h4>Developement</h4></div>
<div class="service-card" style="left:574px"><div class="pic" role="img" aria-label="Blue digital technology background" style="background:linear-gradient(135deg,#0b3d7a,#2a8ad0 55%,#0d4e92)"></div><h4>Enterprise Integration</h4></div>

<svg class="abs" style="left:66px;top:922px" width="8" height="14" viewBox="0 0 8 14"><path d="M7 1L1 7l6 6" fill="none" stroke="#bbb" stroke-width="1.5"/></svg>
<svg class="abs" style="left:726px;top:922px" width="8" height="14" viewBox="0 0 8 14"><path d="M1 1l6 6-6 6" fill="none" stroke="#bbb" stroke-width="1.5"/></svg>
<div class="quote-bg">&ldquo;</div>
<div class="avatar" role="img" aria-label="Portrait photo of the client"></div>
<p class="quote-text">It is a long established fact that a reader will be distracted by the readable content of a page when looking at its layout. The point of using Lorem Ipsum is that it has a more-or-less normal distribution of letters, as opposed to using 'Content here, content here', making it look like readable English.</p>
<p class="quote-name">- Daniel Reyes</p>

<footer class="site-footer">
  <div class="brand footer-brand abs"><span class="brand-dot"></span>BEACON ADVISORY</div>
  <div class="col-rule" style="left:238px"></div>
  <div class="col-rule" style="left:364px"></div>
  <div class="col-rule" style="left:585px"></div>

  <h5 class="col-title" style="left:268px">INFORMATION</h5>
  <ul class="info-links"><li>Home</li><li>Company</li><li>Services</li><li>Solutions</li><li>Resources</li><li>Career</li><li>Contact Us</li></ul>

  <h5 class="col-title" style="left:387px">NEWSLETTER</h5>
  <p class="news-text">Register Your email address to get information ablout us</p>
  <div class="news-input">Email Address</div>
  <div class="btn-subscribe">SUBSCRIBE</div>

  <h5 class="col-title" style="left:607px">CONTACT US</h5>
  <div class="contact-row" style="top:58px">
    <svg width="7" height="10" viewBox="0 0 7 10"><path d="M3.5 0A3.5 3.5 0 0 0 0 3.5C0 6 3.5 10 3.5 10S7 6 7 3.5A3.5 3.5 0 0 0 3.5 0zm0 5a1.5 1.5 0 1 1 0-3 1.5 1.5 0 0 1 0 3z" fill="#fff"/></svg>
    <span>450 Harbor Point Rd Suite 120<br>Westfield, NJ 07090</span>
  </div>
  <div class="contact-row" style="top:97px">
    <svg width="9" height="9" viewBox="0 0 24 24"><path fill="#fff" d="M6.6 10.8a15.1 15.1 0 0 0 6.6 6.6l2.2-2.2c.3-.3.7-.4 1-.2 1.1.4 2.3.6 3.6.6.6 0 1 .4 1 1V20c0 .6-.4 1-1 1A17 17 0 0 1 3 4c0-.6.4-1 1-1h3.5c.6 0 1 .4 1 1 0 1.3.2 2.5.6 3.6.1.3 0 .7-.2 1z"/></svg>
    <span>+1 (555) 014 2290</span>
  </div>
  <div class="contact-row" style="top:123px">
    <svg width="10" height="8" viewBox="0 0 10 8"><rect width="10" height="8" rx="1" fill="#fff"/><path d="M0 1l5 3.5L10 1" fill="none" stroke="#1f2a3a" stroke-width="1"/></svg>
    <span>info@beaconadvisory.com</span>
  </div>

  <div class="footer-rule"></div>
  <p class="copyright">Copyrights &copy; 2016, Beacon Advisory. All rights reserved.</p>
  <div class="socials" aria-label="Social links"><span></span><span></span><span></span><span></span></div>
</footer>

</body>
</html>
```